Velk Partners Building Business Cards

We need a business card that reflects our business as "Solar Experts" in San Diego. Browse our website www.velkpartners.example our License needs to be displayed as "CSLB# 3867140" our phone number is (619) 555-0187

Save thousands on your electric bills and increase the value of your home while helping to protect the environment. Our solar installation experts will help you design the system that's right for you, using only the highest quality equipment that will look great and give you ideal performance. Our goal is to make you energy independent, and get your electric bill to 0.

Paul Osterby
(619) 555-0187
paul@velkpartners.example

Target Market(s)

Home owners in san diego looking for solar

Industry/Entity Type

Solar Energy

Contact Information for Business Card

Paul Osterby
(619) 555-0187
paul@velkpartners.example

Font styles to use
Other font styles liked:
• Use our logo font

Requirements
Must have
• License needs to be displayed as "CSLB# 3867140" our phone number is (619) 555-0187
Nice to have
• Real images of rooftop home solar in san diego
Should not have
• our business address

```html
<!DOCTYPE html>
<html lang="en">
<head>
<meta charset="utf-8">
<title>Velk Partners Building – Business Cards</title>
<link rel="stylesheet" href="https://fonts.googleapis.com/css2?family=Open+Sans:wght@400;600;700&display=swap">
<style>
  :root {
    --page: #eceae6;
    --navy: #1f3c79;
    --navy-deep: #18306a;
    --gold: #f5ad13;
    --ink: #111214;
    --ink-soft: #23252a;
    --white: #ffffff;
    --light-text: #e9e9ea;
  }
  * { box-sizing: border-box; margin: 0; padding: 0; }
  html, body {
    width: 1200px; height: 900px; overflow: hidden;
    background: var(--page);
    font-family: "Open Sans", Arial, sans-serif;
  }
  .canvas { position: relative; width: 1200px; height: 900px; }

  .card {
    position: absolute;
    width: 540px; height: 309px;
    overflow: hidden;
    box-shadow: 0 10px 24px rgba(0,0,0,0.18);
  }

  /* Front */
  .card-front {
    left: 80px; top: 120px;
    background: var(--navy);
    display: flex; align-items: center; justify-content: center;
  }
  .brand {
    display: flex; align-items: center; gap: 12px;
  }
  .brand-dot {
    width: 22px; height: 22px; border-radius: 50%;
    background: var(--gold);
  }
  .brand-name {
    font-weight: 700; font-size: 36px; letter-spacing: -0.5px;
    color: var(--white); white-space: nowrap;
  }

  /* Back */
  .card-back {
    left: 580px; top: 450px;
    background: radial-gradient(ellipse at 40% 30%, var(--ink-soft), var(--ink) 75%);
  }
  .card-back .waves { position: absolute; inset: 0; }
  .holder-name {
    position: absolute; left: 46px; top: 78px;
    font-weight: 700; font-size: 17px; color: var(--gold);
  }
  .back-brand {
    position: absolute; right: 26px; top: 62px;
    display: flex; align-items: center; gap: 8px;
  }
  .back-brand .brand-dot { width: 14px; height: 14px; }
  .back-brand .brand-name { font-size: 24px; color: var(--navy); }

  .contact {
    position: absolute; left: 40px; top: 188px;
    list-style: none;
  }
  .contact li {
    display: flex; align-items: center; gap: 8px;
    font-size: 14px; color: var(--light-text); line-height: 24px;
  }
  .contact svg { width: 12px; height: 12px; flex: none; }

  .license {
    position: absolute; right: 24px; top: 222px;
    font-weight: 600; font-size: 14px; color: var(--gold);
  }
</style>
</head>
<body>
<main class="canvas">

  <section class="card card-front" aria-label="Card front">
    <div class="brand">
      <span class="brand-dot"></span>
      <span class="brand-name">Velk Partners Building</span>
    </div>
  </section>

  <section class="card card-back" aria-label="Card back">
    <svg class="waves" viewBox="0 0 540 309" preserveAspectRatio="none" aria-hidden="true">
      <path d="M0,309 L0,298 C160,298 320,232 420,182 C470,160 510,150 540,148 L540,309 Z" fill="var(--navy)"/>
      <path d="M0,266 C140,272 270,240 345,196 C300,244 170,286 0,288 Z" fill="var(--gold)"/>
    </svg>

    <p class="holder-name">Paul Osterby</p>

    <div class="back-brand">
      <span class="brand-dot"></span>
      <span class="brand-name">Velk Partners Building</span>
    </div>

    <ul class="contact">
      <li>
        <svg viewBox="0 0 24 24" aria-hidden="true"><path fill="var(--gold)" d="M6.6 10.8a15.1 15.1 0 0 0 6.6 6.6l2.2-2.2c.3-.3.7-.4 1-.2 1.1.4 2.3.6 3.6.6.6 0 1 .4 1 1V20c0 .6-.4 1-1 1A17 17 0 0 1 3 4c0-.6.4-1 1-1h3.5c.6 0 1 .4 1 1 0 1.3.2 2.5.6 3.6.1.3 0 .7-.2 1z"/></svg>
        (619) 555-0187
      </li>
      <li>
        <svg viewBox="0 0 24 24" aria-hidden="true"><path fill="var(--gold)" d="M2 5h20v14H2z"/><path d="M2 5l10 8 10-8" fill="none" stroke="var(--ink)" stroke-width="2"/></svg>
        paul@velkpartners.example
      </li>
    </ul>

    <p class="license">License: CSLB# 3867140</p>
  </section>

</main>
</body>
</html>
```